Home Multi-Service Company Website

I currently have only a landing page but am looking for someone to build out a nice, modern looking website that will cover multiple services we offer like Landscape Lighting, Gutter Cleaning, Holiday Lighting, Window Cleaning, Insulation Services like Blow In and Removal, Blower Door Tests, Rodent Exclusion and Trapping and others. We would also like our Holiday lighting category to have links to a separate page for franchise opportunities.

Target Market(s)

Home

Font styles to use
Serif
Sans Serif

Requirements
Must have
• A modern and organized look. Detailed information regarding each service provided by our company.
Nice to have
• We are a service company so would like to see options to link reviews from trevolo and maybe some nice pictures of people at home. We would like the color to match our logo as well.

```html
<!DOCTYPE html>
<html lang="en">
<head>
<meta charset="utf-8">
<title>Brightline Services</title>
<link href="https://fonts.googleapis.com/css2?family=Poppins:wght@600;700&family=Roboto:wght@400;500&display=swap" rel="stylesheet">
<style>
:root{
  --navy:#3f4359;
  --navy-dark:#2f3244;
  --ink:#1d1f2a;
  --text:#5b5e6b;
  --light:#ffffff;
  --card:#f3f3f3;
  --star:#e8731c;
  --head:'Poppins',sans-serif;
  --body:'Roboto',sans-serif;
}
*{box-sizing:border-box;margin:0;padding:0}
html,body{width:1200px;height:3775px;overflow:hidden}
body{font-family:var(--body);color:var(--text);background:#fff;position:relative}
.wrap{width:978px;margin:0 auto;position:relative}
a{text-decoration:none;color:inherit}
.btn{display:inline-flex;align-items:center;gap:8px;background:var(--navy);color:#fff;font:500 14px var(--body);text-transform:uppercase;padding:0 20px;height:44px;border-radius:2px}
.btn .arrow{width:13px;height:13px;border-radius:50%;background:#fff;position:relative}
.btn .arrow::after{content:"";position:absolute;left:4px;top:3.5px;border-left:5px solid var(--navy);border-top:3px solid transparent;border-bottom:3px solid transparent}
.btn.dark{background:var(--ink)}
.btn.dark .arrow::after{border-left-color:var(--ink)}
h2{font:700 42px/1.05 var(--head);color:var(--navy)}

/* header */
.site-header{height:96px}
.site-header .wrap{display:flex;align-items:center;height:96px}
.brand{display:flex;align-items:center;gap:10px;font:700 28px var(--head);color:var(--navy);width:236px}
.brand .mark{width:22px;height:22px;background:var(--navy)}
.nav{display:flex;gap:19px;font:500 14.5px var(--body);color:var(--ink)}
.nav a.active{position:relative}
.nav a.active::after{content:"";position:absolute;left:0;right:0;bottom:-12px;height:3px;background:var(--navy)}
.site-header .btn{margin-left:auto;height:45px;font-size:15px;text-transform:none;padding:0 19px}

/* hero */
.hero{height:586px;position:relative;text-align:center;color:#fff;
  background:linear-gradient(180deg,#2e3a2a 0%,#4f6a36 35%,#7d7f6e 70%,#9c9a94 100%)}
.hero h1{font:700 42px var(--head);padding-top:187px}
.hero p{font:500 16.5px/1.65 var(--body);width:500px;margin:14px auto 0}
.hero .btn{margin-top:25px;height:49px;padding:0 34px;font-size:16px;text-transform:uppercase;background:#424553}

/* about */
.about{height:680px}
.about .wrap{height:680px}
.about-copy{position:absolute;left:0;top:190px;width:390px}
.about-copy p{font:400 13.5px/1.9 var(--body);margin:24px 0 26px}
.about-photo{position:absolute;left:489px;top:92px;width:488px;height:496px;background:linear-gradient(135deg,#8a8f86,#c9cfc4 50%,#5b6477)}

/* services */
.services{height:395px;background:linear-gradient(90deg,#3b3f52 0%,#46495a 55%,#55596a 80%,#4a4e63 100%);color:#fff;text-align:center}
.services h2{color:#fff;padding-top:55px;font-size:40px}
.svc-grid{display:grid;grid-template-columns:repeat(4,267px);justify-content:center;margin-top:42px}
.svc svg{width:56px;height:56px;stroke:#fff;fill:none;stroke-width:2}
.svc h3{font:500 16.5px var(--body);margin:14px 0 10px}
.svc p{font:400 14px/1.6 var(--body);padding:0 16px}

/* insulation */
.insulation{height:683px;text-align:center}
.insulation h2{padding-top:83px}
.ins-grid{display:grid;grid-template-columns:repeat(3,309px);gap:25px;justify-content:center;margin-top:39px}
.ins-photo{height:213px}
.ins-card h3{font:500 16.5px var(--body);color:var(--ink);margin:28px 0 14px}
.ins-card p{font:400 14px/1.75 var(--body);padding:0 20px}
.ins-card .btn{margin-top:24px;height:43px}

/* canadian */
.proud{height:349px;text-align:center;color:#fff;background:linear-gradient(90deg,#2f3a22,#6f4a2e 45%,#4c5a2f 70%,#2a3620)}
.proud h2{color:#fff;padding-top:55px;font-size:40px;line-height:1.15}
.proud p{font:400 14px/1.95 var(--body);width:840px;margin:16px auto 0}
.proud .btn{margin-top:16px}

/* reviews */
.reviews{height:536px;text-align:center}
.reviews h2{padding-top:92px}
.rev-grid{display:grid;grid-template-columns:repeat(3,312px);gap:21px;justify-content:center;margin-top:40px}
.rev{background:var(--card);height:261px;padding-top:36px}
.rev h3{font:500 15px var(--body);color:var(--ink)}
.rev time{display:block;font-size:12px;color:#888;margin-top:4px}
.stars{display:flex;justify-content:center;gap:2px;margin-top:8px}
.stars svg{width:13px;height:13px;fill:var(--star)}
.rev p{font:400 14px/1.85 var(--body);padding:0 28px;margin-top:14px}

/* cta */
.cta{height:268px;background:var(--navy);text-align:center;color:#fff}
.cta h2{color:#fff;padding-top:62px;font-size:40px}
.cta p{font:400 15px/1.7 var(--body);width:760px;margin:10px auto 0}
.cta .btn{margin-top:18px;height:47px}

/* footer */
.site-footer{height:182px}
.site-footer .wrap{height:182px}
.site-footer .brand{position:absolute;left:0;top:70px;font-size:32px}
.foot-links{position:absolute;right:0;top:60px;display:flex;gap:14px;font:400 13.5px var(--body);color:var(--text)}
.foot-links span{color:#999}
.copy{position:absolute;left:363px;top:108px;font-size:13.5px}
.social{position:absolute;right:0;top:97px;display:flex;gap:8px}
.social i{width:34px;height:34px;border:2px solid var(--ink);border-radius:50%;display:block}
</style>
</head>
<body>

<header class="site-header">
  <div class="wrap">
    <a class="brand" href="#"><span class="mark"></span>Brightline</a>
    <nav class="nav">
      <a class="active" href="#">Home</a><a href="#">About Us</a><a href="#">Services</a><a href="#">Reviews</a><a href="#">Holiday lighting category</a><a href="#">Contact Us</a>
    </nav>
    <a class="btn" href="#">Service Request</a>
  </div>
</header>

<section class="hero" role="img" aria-label="Evening garden path lit by landscape lights">
  <h1>Brightline Services</h1>
  <p>Lorem ipsum dolor sit amet, consectetur adipiscing elit, sed do eiusmod tempor incididunt ut magna aliqua.</p>
  <a class="btn" href="#">Get Started</a>
</section>

<section class="about">
  <div class="wrap">
    <div class="about-copy">
      <h2>About&nbsp; Brightline Services</h2>
      <p>Lorem ipsum dolor sit amet, consectetur adipiscing elit, sed do eiusmod tempor incididunt ut labore et dolore magna aliqua. Ut enim ad minim veniam, quis nostrud exercitation ullamco laboris aliquip ex ea consequat.</p>
      <a class="btn" href="#">Learn More <span class="arrow"></span></a>
    </div>
    <div class="about-photo" role="img" aria-label="Two cleaners in overalls washing a glass door and floor"></div>
  </div>
</section>

<section class="services">
  <h2>Our Services</h2>
  <div class="svc-grid">
    <div class="svc">
      <svg viewBox="0 0 56 56"><path d="M6 10h44M14 10v4h28v-4M28 18v6M22 22l-3-3M34 22l3-3M14 44c4-8 10-8 14 0c4-8 10-8 14 0M6 48h44"/><circle cx="28" cy="28" r="3"/></svg>
      <h3>Landscape Lighting</h3>
      <p>Sed ut perspiciatis unde omnis iste error sit voluptatem accusantium doloremque totam rem</p>
    </div>
    <div class="svc">
      <svg viewBox="0 0 56 56"><path d="M6 10h44v8H30v30h-8V24c0-4-4-6-8-6H6z"/></svg>
      <h3>Gutter Cleaning</h3>
      <p>Sed ut perspiciatis unde omnis iste error sit voluptatem accusantium doloremque totam rem</p>
    </div>
    <div class="svc">
      <svg viewBox="0 0 56 56"><path d="M10 8v18c0 6 6 10 12 10h6M16 8v12M22 8v10M28 12v10"/><circle cx="36" cy="34" r="8"/><path d="M36 20v-4M48 34h4M44 24l3-3M44 44l3 3M36 48v4"/></svg>
      <h3>Holiday Lighting</h3>
      <p>Sed ut perspiciatis unde omnis iste error sit voluptatem accusantium doloremque totam rem</p>
    </div>
    <div class="svc">
      <svg viewBox="0 0 56 56"><rect x="8" y="4" width="40" height="48"/><rect x="14" y="10" width="28" height="36"/><path d="M28 10v36M20 18l2 2M36 30l2 2"/></svg>
      <h3>Window Cleaning</h3>
      <p>Sed ut perspiciatis unde omnis iste error sit voluptatem accusantium doloremque totam rem</p>
    </div>
  </div>
</section>

<section class="insulation">
  <h2>Insulation Services</h2>
  <div class="ins-grid">
    <article class="ins-card">
      <div class="ins-photo" role="img" aria-label="Worker clearing deep snow with a snow blower" style="background:linear-gradient(135deg,#cfdcef,#f2f5fa 60%,#8ea6cf)"></div>
      <h3>Blow In and Removal</h3>
      <p>Lorem ipsum dolor sit amet, consectetur adipiscing elit, sed do eiusmod tempor incididunt ut labore dolore</p>
      <a class="btn" href="#">Read More <span class="arrow"></span></a>
    </article>
    <article class="ins-card">
      <div class="ins-photo" role="img" aria-label="Technician setting up a red blower door fan in a doorway" style="background:linear-gradient(90deg,#e8e2dc,#c0262a 40%,#8d1c20 60%,#e6e2de)"></div>
      <h3>Blower Door Tests</h3>
      <p>Lorem ipsum dolor sit amet, consectetur adipiscing elit, sed do eiusmod tempor incididunt ut labore dolore</p>
      <a class="btn" href="#">Read More <span class="arrow"></span></a>
    </article>
    <article class="ins-card">
      <div class="ins-photo" role="img" aria-label="Wire mesh guard fitted over a house wall vent" style="background:linear-gradient(135deg,#c7d0dc,#7d8899 50%,#dfe4ea)"></div>
      <h3>Rodent Exclusion and Trapping</h3>
      <p>Lorem ipsum dolor sit amet, consectetur adipiscing elit, sed do eiusmod tempor incididunt ut labore dolore</p>
      <a class="btn" href="#">Read More <span class="arrow"></span></a>
    </article>
  </div>
</section>

<section class="proud" role="img" aria-label="Garden path lit by warm landscape lights at dusk">
  <h2>Reliable. Proudly Canadian.<br>Environmentally-conscious.</h2>
  <p>Lorem ipsum dolor sit amet, consectetur adipiscing elit, sed do eiusmod tempor incididunt ut labore et dolore magna aliqua. Ut enim ad minim veniam, quis nostrud exercitation ullamco</p>
  <a class="btn" href="#">Get Started <span class="arrow"></span></a>
</section>

<section class="reviews">
  <h2>Trevolo Reviews</h2>
  <div class="rev-grid">
    <article class="rev">
      <h3>John Doe</h3><time>2 days ago</time>
      <div class="stars"><svg viewBox="0 0 24 24"><path d="M12 2l3 7h7l-5.5 4.5 2 7.5L12 17l-6.5 4 2-7.5L2 9h7z"/></svg><svg viewBox="0 0 24 24"><path d="M12 2l3 7h7l-5.5 4.5 2 7.5L12 17l-6.5 4 2-7.5L2 9h7z"/></svg><svg viewBox="0 0 24 24"><path d="M12 2l3 7h7l-5.5 4.5 2 7.5L12 17l-6.5 4 2-7.5L2 9h7z"/></svg><svg viewBox="0 0 24 24"><path d="M12 2l3 7h7l-5.5 4.5 2 7.5L12 17l-6.5 4 2-7.5L2 9h7z"/></svg><svg viewBox="0 0 24 24"><path d="M12 2l3 7h7l-5.5 4.5 2 7.5L12 17l-6.5 4 2-7.5L2 9h7z"/></svg></div>
      <p>Lorem ipsum sit consectetur adipiscing elit, sed do eiusmod tempor incididunt ut labore et&nbsp; magna aliqua.</p>
    </article>
    <article class="rev">
      <h3>John Doe</h3><time>2 days ago</time>
      <div class="stars"><svg viewBox="0 0 24 24"><path d="M12 2l3 7h7l-5.5 4.5 2 7.5L12 17l-6.5 4 2-7.5L2 9h7z"/></svg><svg viewBox="0 0 24 24"><path d="M12 2l3 7h7l-5.5 4.5 2 7.5L12 17l-6.5 4 2-7.5L2 9h7z"/></svg><svg viewBox="0 0 24 24"><path d="M12 2l3 7h7l-5.5 4.5 2 7.5L12 17l-6.5 4 2-7.5L2 9h7z"/></svg><svg viewBox="0 0 24 24"><path d="M12 2l3 7h7l-5.5 4.5 2 7.5L12 17l-6.5 4 2-7.5L2 9h7z"/></svg><svg viewBox="0 0 24 24"><path d="M12 2l3 7h7l-5.5 4.5 2 7.5L12 17l-6.5 4 2-7.5L2 9h7z"/></svg></div>
      <p>Lorem ipsum sit consectetur adipiscing elit, sed do eiusmod tempor incididunt ut labore et&nbsp; magna aliqua.</p>
    </article>
    <article class="rev">
      <h3>John Doe</h3><time>2 days ago</time>
      <div class="stars"><svg viewBox="0 0 24 24"><path d="M12 2l3 7h7l-5.5 4.5 2 7.5L12 17l-6.5 4 2-7.5L2 9h7z"/></svg><svg viewBox="0 0 24 24"><path d="M12 2l3 7h7l-5.5 4.5 2 7.5L12 17l-6.5 4 2-7.5L2 9h7z"/></svg><svg viewBox="0 0 24 24"><path d="M12 2l3 7h7l-5.5 4.5 2 7.5L12 17l-6.5 4 2-7.5L2 9h7z"/></svg><svg viewBox="0 0 24 24"><path d="M12 2l3 7h7l-5.5 4.5 2 7.5L12 17l-6.5 4 2-7.5L2 9h7z"/></svg><svg viewBox="0 0 24 24"><path d="M12 2l3 7h7l-5.5 4.5 2 7.5L12 17l-6.5 4 2-7.5L2 9h7z"/></svg></div>
      <p>Lorem ipsum sit consectetur adipiscing elit, sed do eiusmod tempor incididunt ut labore et&nbsp; magna aliqua.</p>
    </article>
  </div>
</section>

<section class="cta">
  <h2>Ready To Get Started?</h2>
  <p>Lorem ipsum dolor sit amet, consectetur adipiscing elit, sed do eiusmod tempor incididunt ut labore et dolore magna aliqua. Ut enim ad minim veniam, quis nostrud exercitation</p>
  <a class="btn dark" href="#">Contact Us <span class="arrow"></span></a>
</section>

<footer class="site-footer">
  <div class="wrap">
    <a class="brand" href="#"><span class="mark"></span>Brightline</a>
    <nav class="foot-links">
      <a href="#">Home</a><span>|</span><a href="#">About Us</a><span>|</span><a href="#">Services</a><span>|</span><a href="#">Blog</a><span>|</span><a href="#">Holiday lighting category</a><span>|</span><a href="#">Contact Us</a>
    </nav>
    <p class="copy">© 2021&nbsp; Brightline Services&nbsp; |&nbsp; All Rights Reserved</p>
    <div class="social" aria-label="Social links"><i></i><i></i><i></i><i></i></div>
  </div>
</footer>

</body>
</html>
```